Dario Lenti Pools , pool construction for residential properties and pool renovations

I have been involved in the pool industry for over 20years and looking to start my own buisnes. My brother and I are teaming up together to make this happen . We will be doing pool renovations to existing old pools "pool makeovers" and also owner builder pools which will save a lot of money in overall cost of a new pool construction. Cards need to be creative not a generic photo of pool ,let's be different.

Target Market(s)

Home owners

Industry/Entity Type

Pool Service

Contact Information for Business Card

Owner builder pools , Pool renovations

Font styles to use
Sans Serif

Colors

Designer to choose colors to be used in the design.

Requirements
Must have
• Mobile number , web , email
Nice to have
• Be creative

```html
<!DOCTYPE html>
<html lang="en">
<head>
<meta charset="utf-8">
<title>Dario Lenti Pools – Business Card</title>
<link rel="stylesheet" href="https://fonts.googleapis.com/css2?family=Montserrat:wght@400;600&display=swap">
<style>
  :root {
    --backdrop: #e9e9e9;
    --card-white: #f4f4f4;
    --brand-blue: #1c8fd6;
    --ink: #2b2b2b;
    --water-light: #4cc3f0;
    --water-mid: #159ddf;
    --water-deep: #1f4fc4;
    --water-navy: #1a2f9c;
    --on-water: #ffffff;
  }
  * { margin: 0; padding: 0; box-sizing: border-box; }
  html, body {
    width: 1200px;
    height: 720px;
    overflow: hidden;
    background: var(--backdrop);
    font-family: "Montserrat", sans-serif;
  }
  .card {
    position: absolute;
    left: 150px;
    top: 90px;
    width: 900px;
    height: 540px;
    background: var(--card-white);
    overflow: hidden;
    box-shadow: 0 12px 30px rgba(0, 0, 0, 0.12);
  }
  .card__water {
    position: absolute;
    inset: 0;
    width: 900px;
    height: 540px;
  }
  .brand {
    position: absolute;
    left: 62px;
    top: 44px;
    color: var(--brand-blue);
    font-weight: 600;
    font-size: 64px;
    line-height: 0.95;
    letter-spacing: -1px;
  }
  .brand__dot {
    display: inline-block;
    width: 22px;
    height: 22px;
    border-radius: 50%;
    background: var(--brand-blue);
    margin-left: 10px;
    vertical-align: middle;
  }
  .contacts {
    position: absolute;
    left: 66px;
    top: 282px;
    list-style: none;
    color: var(--ink);
    font-size: 22px;
    font-weight: 400;
  }
  .contacts__item {
    display: flex;
    align-items: center;
    gap: 14px;
    height: 32px;
  }
  .contacts__icon {
    width: 18px;
    height: 18px;
    flex: none;
  }
  .services {
    position: absolute;
    left: 380px;
    top: 360px;
    list-style: none;
    color: var(--on-water);
    font-size: 22px;
    font-weight: 400;
    letter-spacing: 1px;
    line-height: 1.55;
    text-transform: uppercase;
  }
  .services__item:first-child { padding-left: 0; }
  .services__item:last-child { padding-left: 0; }
</style>
</head>
<body>
  <main class="card">
    <svg class="card__water" viewBox="0 0 900 540" role="img" aria-label="Sparkling pool water in bright turquoise and deep blue tones">
      <defs>
        <linearGradient id="waterLight" x1="0" y1="1" x2="1" y2="0">
          <stop offset="0" stop-color="#38b4ec"/>
          <stop offset="0.5" stop-color="#4cc3f0"/>
          <stop offset="1" stop-color="#1d9ee0"/>
        </linearGradient>
        <linearGradient id="waterDeep" x1="0" y1="0" x2="1" y2="1">
          <stop offset="0" stop-color="#1f63d6"/>
          <stop offset="0.6" stop-color="#1f4fc4"/>
          <stop offset="1" stop-color="#1a2f9c"/>
        </linearGradient>
      </defs>
      <path class="water-band" d="M0,540 L0,430 C160,390 300,340 400,270 C500,195 560,80 720,30 C790,10 850,2 900,0 L900,540 Z" fill="url(#waterLight)"/>
      <path class="water-band water-band--mid" d="M330,540 C430,470 470,380 560,280 C640,190 760,140 900,120 L900,540 Z" fill="#2aa6e6" opacity="0.55"/>
      <path class="water-band water-band--deep" d="M600,540 C640,430 690,300 900,200 L900,540 Z" fill="url(#waterDeep)"/>
    </svg>

    <h1 class="brand">Dario<br>Lenti<br>Pools<span class="brand__dot"></span></h1>

    <ul class="contacts">
      <li class="contacts__item">
        <svg class="contacts__icon" viewBox="0 0 18 18" aria-hidden="true">
          <rect x="4.5" y="1" width="9" height="16" rx="1.5" fill="none" stroke="var(--brand-blue)" stroke-width="1.6"/>
          <circle cx="9" cy="14" r="1" fill="var(--brand-blue)"/>
        </svg>
        Mobile number
      </li>
      <li class="contacts__item">
        <svg class="contacts__icon" viewBox="0 0 18 18" aria-hidden="true">
          <rect x="1" y="3.5" width="16" height="11" fill="none" stroke="var(--brand-blue)" stroke-width="1.6"/>
          <path d="M1 3.5 L9 10 L17 3.5" fill="none" stroke="var(--brand-blue)" stroke-width="1.6"/>
        </svg>
        email
      </li>
      <li class="contacts__item">
        <svg class="contacts__icon" viewBox="0 0 18 18" aria-hidden="true">
          <circle cx="9" cy="9" r="7.5" fill="none" stroke="var(--brand-blue)" stroke-width="1.6"/>
          <ellipse cx="9" cy="9" rx="3.2" ry="7.5" fill="none" stroke="var(--brand-blue)" stroke-width="1.3"/>
          <path d="M1.5 9 H16.5 M3 5 H15 M3 13 H15" stroke="var(--brand-blue)" stroke-width="1.2"/>
        </svg>
        web
      </li>
    </ul>

    <ul class="services">
      <li class="services__item">Pool Renovations</li>
      <li class="services__item">New Pool Construction</li>
    </ul>
  </main>
</body>
</html>
```